Flyers

Modify Existing Flyer and create another for exterior company
Updates

Previous Brief has been updated- we want to update this existing one also

Target Market(s)

Exterior Remodeling Customers

Industry/Entity Type

Remodeling/Construction

```html
<!DOCTYPE html>
<html lang="en">
<head>
<meta charset="utf-8">
<title>Northfield Roofing &amp; Exteriors – Remodeling Flyer</title>
<link href="https://fonts.googleapis.com/css2?family=Baloo+2:wght@700;800&family=Montserrat:wght@400;500;600&display=swap" rel="stylesheet">
<style>
  :root{
    --roof-blue:#2f7fe6;
    --navy:#14209a;
    --orange:#fb3a16;
    --ink:#1f1f1f;
    --grey:#6f6f6f;
    --bullet:#9a9a9a;
    --white:#ffffff;
  }
  *{margin:0;padding:0;box-sizing:border-box}
  html,body{width:849px;height:1200px;overflow:hidden;background:var(--white)}
  .flyer{position:relative;width:849px;height:1200px;overflow:hidden;background:var(--white);
    font-family:"Montserrat",Arial,sans-serif;color:var(--ink)}
  .abs{position:absolute}

  /* header */
  .hero-art{position:absolute;left:0;top:0;width:849px;height:513px}
  .brand{left:22px;top:26px;display:flex;align-items:center;gap:8px}
  .brand-mark{width:12px;height:12px;background:var(--orange)}
  .brand-name{font-family:"Baloo 2",Arial,sans-serif;font-weight:800;color:var(--orange);
    font-size:17px;line-height:1.05;letter-spacing:.2px}
  .contact{right:22px;top:21px;text-align:right}
  .contact .cta{font-size:12.6px;color:var(--grey);line-height:1.2;letter-spacing:.2px}
  .contact .phone{font-family:"Baloo 2",Arial,sans-serif;font-weight:800;font-size:28px;color:var(--navy);
    line-height:1.05;margin-top:2px}
  .contact .web{font-size:12.6px;color:var(--grey);letter-spacing:.3px}
  .room-label{font-family:"Baloo 2",Arial,sans-serif;font-weight:800;color:var(--white);
    font-size:46px;line-height:1;top:458px}

  /* orange band */
  .promo-band{left:0;top:513px;width:849px;height:129px;background:var(--orange)}
  .promo-text{left:30px;top:530px;color:var(--white)}
  .promo-text .lead{font-size:21.5px;font-weight:500;line-height:1.1;letter-spacing:.3px}
  .promo-text .title{font-family:"Baloo 2",Arial,sans-serif;font-weight:800;font-size:40px;line-height:1;margin-top:4px}
  .promo-text .place{font-size:21px;font-weight:500;margin-top:4px}
  .feature-photo{left:524px;top:538px;width:313px;height:313px;border-radius:50%;
    border:6px solid var(--white);
    background:radial-gradient(circle at 50% 58%,#f6f3ee 0 30%,#d7ba8e 55%,#a9773f 90%)}

  /* service blocks */
  .section-title{font-family:"Baloo 2",Arial,sans-serif;font-weight:800;color:var(--navy);
    font-size:25px;line-height:1;letter-spacing:.2px}
  .section-copy{font-size:12.4px;line-height:1.28}
  .icon-slot{background:#ffe3dc;border-radius:6px}
  .bullets{list-style:none;font-size:12.6px;line-height:18.5px}
  .bullets li{position:relative;padding-left:16px;white-space:nowrap}
  .bullets li::before{content:"";position:absolute;left:0;top:6px;width:6px;height:6px;
    background:radial-gradient(circle,var(--bullet) 1px,transparent 1.4px) 0 0/3px 3px}

  /* bathroom band */
  .bath-band{left:0;top:1072px;width:849px;height:128px;background:var(--roof-blue);color:var(--white)}
  .bath-band .section-title{color:var(--white);font-size:26px}
  .bath-band .bullets li::before{background:radial-gradient(circle,#cfe0fb 1px,transparent 1.4px) 0 0/3px 3px}
</style>
</head>
<body>
<div class="flyer">

  <svg class="hero-art" viewBox="0 0 849 513" aria-hidden="false">
    <defs>
      <linearGradient id="kitchenTones" x1="0" y1="0" x2="1" y2="1">
        <stop offset="0" stop-color="#e9d8bf"/>
        <stop offset=".45" stop-color="#b77f4c"/>
        <stop offset="1" stop-color="#6a4426"/>
      </linearGradient>
      <linearGradient id="bathTones" x1="0" y1="0" x2="1" y2="1">
        <stop offset="0" stop-color="#1a1a1c"/>
        <stop offset=".6" stop-color="#2f2f33"/>
        <stop offset="1" stop-color="#bfbfbf"/>
      </linearGradient>
    </defs>
    <polygon points="0,185 410,0 849,183 849,190 415,51 408,51 0,190" fill="var(--roof-blue)"/>
    <polygon role="img" aria-label="Photo of a remodeled kitchen with wood cabinets and granite counters"
      points="0,190 408,51 408,513 0,513" fill="url(#kitchenTones)"/>
    <polygon role="img" aria-label="Photo of a modern bathroom with black marble walls and double vanity"
      points="415,51 849,190 849,513 415,513" fill="url(#bathTones)"/>
    <rect x="0" y="445" width="408" height="68" fill="#1b1b1b" opacity=".72"/>
    <rect x="415" y="445" width="434" height="68" fill="#1b1b1b" opacity=".72"/>
  </svg>

  <div class="abs brand">
    <span class="brand-mark"></span>
    <div class="brand-name">NORTHFIELD<br>ROOFING &amp; EXTERIORS</div>
  </div>

  <div class="abs contact">
    <div class="cta">CALL TODAY FOR YOUR<br>FREE ESTIMATE</div>
    <div class="phone">555-014-2280</div>
    <div class="web">WWW.NORTHFIELDEXTERIORS.COM</div>
  </div>

  <div class="abs room-label" style="left:28px">Kitchen</div>
  <div class="abs room-label" style="left:442px">Bathroom?</div>

  <div class="abs promo-band"></div>
  <div class="abs promo-text">
    <div class="lead">Work with a Top-rated Local</div>
    <div class="title">Remodeling Company</div>
    <div class="place">in Ankeny, IA</div>
  </div>
  <div class="abs feature-photo" role="img" aria-label="Photo of a freestanding white soaking tub in a stone-tiled bathroom"></div>

  <!-- Kitchen remodeling -->
  <h2 class="abs section-title" style="left:30px;top:684px">KITCHEN REMODELING</h2>
  <div class="abs icon-slot" role="img" aria-label="Kitchen icon" style="left:389px;top:685px;width:60px;height:58px"></div>
  <p class="abs section-copy" style="left:30px;top:714px;width:360px">Whatever your vision is for your new kitchen,<br>our crew can help you bring it to life. You can trust us for:</p>
  <ul class="abs bullets" style="left:30px;top:756px">
    <li>Open concept design services</li>
    <li>Kitchen cabinet installation services</li>
    <li>Kitchen countertop installation services</li>
    <li>Lighting installation services</li>
    <li>Tile installation services</li>
  </ul>
  <ul class="abs bullets" style="left:312px;top:756px">
    <li>Plumbing upgrade services</li>
    <li>Electrical upgrade services</li>
    <li>Drywall services</li>
    <li>Painting services</li>
  </ul>

  <!-- Home additions -->
  <h2 class="abs section-title" style="left:33px;top:886px">HOME ADDITIONS</h2>
  <div class="abs icon-slot" role="img" aria-label="House addition icon" style="left:294px;top:889px;width:65px;height:64px"></div>
  <p class="abs section-copy" style="left:33px;top:916px;width:255px">No matter what kind of space you need, our team will bring your vision to life. You can hire us if you need a:</p>
  <ul class="abs bullets" style="left:36px;top:973px">
    <li>Bathroom addition</li>
    <li>Bedroom addition</li>
    <li>Garage addition</li>
    <li>Basement addition</li>
  </ul>
  <ul class="abs bullets" style="left:204px;top:973px">
    <li>Guest room addition</li>
    <li>Living room addition</li>
    <li>Sunroom addition</li>
  </ul>

  <!-- Decks / patios -->
  <div class="abs icon-slot" role="img" aria-label="Patio table and umbrella icon" style="left:421px;top:872px;width:64px;height:58px"></div>
  <h2 class="abs section-title" style="left:502px;top:869px">DECKS/PATIOS</h2>
  <p class="abs section-copy" style="left:502px;top:898px;width:250px">An outdoor space is a great addition to any residential property. When you decide to build a patio or deck, you'll be able to experience a variety of benefits. Your outdoor area will increase your:</p>
  <ul class="abs bullets" style="left:502px;top:985px;font-size:12px">
    <li>Property value</li>
    <li>Curb appeal</li>
    <li>Functional living space</li>
  </ul>

  <!-- Bathroom remodeling -->
  <div class="abs bath-band"></div>
  <svg class="abs" style="left:50px;top:1101px" width="58" height="58" viewBox="0 0 58 58" role="img" aria-label="Bathtub icon"
       fill="none" stroke="#fff" stroke-width="2.2" stroke-linecap="round" stroke-linejoin="round">
    <path d="M4 30h50v6a12 12 0 0 1-12 12H16A12 12 0 0 1 4 36z"/>
    <path d="M12 30V10a6 6 0 0 1 12 0"/>
    <path d="M19 14h10"/>
    <path d="M14 48l-3 6M44 48l3 6"/>
  </svg>
  <h2 class="abs section-title" style="left:130px;top:1098px;color:#fff;font-size:26px">BATHROOM REMODELING</h2>
  <p class="abs section-copy" style="left:130px;top:1130px;width:330px;color:#fff">When you hire us for your bathroom remodeling project, the possibilities are endless. Our experienced and talented team can:</p>
  <ul class="abs bullets" style="left:497px;top:1098px;color:#fff">
    <li>Install a custom tile shower</li>
    <li>Build a new vanity</li>
    <li>Install flooring and tile</li>
    <li>Replace your plumbing and light fixtures</li>
  </ul>
</div>
</body>
</html>
```